Lorvex Tilo medical cannibis cultivation company

tag - Tilo rise
Lorvex Tilo medical cannabis cultivation - logo is selected- can we please see bold examples with our selection. We are mainly dealing with medical companies and professionals. We would like to be stand out in the crowd with our designs. Welcome any and all attempts. Thanks

Target Market(s)

Medical and Professional

Industry/Entity Type

Medical And Science

Font styles to use
Sans Serif

Colors

Designer to choose colors to be used in the design.

Requirements
Must have
• Bright colour and be bold- Love the teal and magenta that is currently on the dark background design.
Nice to have
• shading and the 3D affect- The shadowed appearance.
Should not have
• Anything related to illegal activity or un professional manners

```html
<!DOCTYPE html>
<html lang="en">
<head>
<meta charset="utf-8">
<title>Lorvex Tilo — Stationery Set</title>
<link rel="stylesheet" href="https://fonts.googleapis.com/css2?family=Open+Sans:wght@300;400;600&display=swap">
<style>
  :root{
    --teal:#1a9ba7;
    --magenta:#d8438b;
    --dusk:#8a8aa6;
    --ink:#3a3a3a;
    --muted:#8c8c8c;
    --paper:#ffffff;
    --bg:#e4e4e6;
    --mark-pink:#f6dbe7;
    --mark-teal:#dcf0f1;
  }
  *{box-sizing:border-box;margin:0;padding:0}
  html,body{width:1200px;height:1200px;overflow:hidden}
  body{background:radial-gradient(circle at 50% 40%,#f4f4f5,var(--bg));font-family:"Open Sans",sans-serif;color:var(--ink);position:relative}

  .sheet{position:absolute;background:var(--paper);box-shadow:0 10px 30px rgba(0,0,0,.12);overflow:hidden}

  /* brand lockup */
  .brand{display:flex;flex-direction:column;align-items:center;gap:3px}
  .brand__row{display:flex;align-items:center;gap:8px}
  .brand__dot{border:2px solid var(--teal);border-radius:50%}
  .brand__name{font-weight:600;color:var(--teal);letter-spacing:.5px;white-space:nowrap}
  .brand__tag{font-size:8px;letter-spacing:3px;text-transform:uppercase;color:var(--muted);border-top:1px solid #c9c9c9;padding-top:2px}

  /* letterhead */
  .letterhead{left:60px;top:204px;width:560px;height:792px}
  .letterhead .brand{position:absolute;top:52px;left:0;right:0}
  .letterhead .brand__dot{width:26px;height:26px}
  .letterhead .brand__name{font-size:24px}
  .watermark{position:absolute;border-radius:50%;}
  .letterhead .watermark{left:140px;top:330px;width:300px;height:300px;
    background:radial-gradient(circle at 35% 55%,var(--mark-pink),transparent 60%),radial-gradient(circle at 65% 40%,var(--mark-teal),transparent 60%)}
  .letter{position:absolute;left:56px;top:190px;width:450px;font-size:11px;line-height:1.75;color:#444}
  .letter__to{margin-bottom:26px}
  .letter p{margin-bottom:16px}
  .letter__close{margin-top:30px}
  .signature{display:block;width:150px;height:40px;margin-top:8px;border-radius:20px;background:linear-gradient(90deg,rgba(58,58,58,.18),rgba(58,58,58,.05))}
  .letterhead__wave{position:absolute;left:0;bottom:0;width:560px;height:260px}
  .letterhead__contact{position:absolute;right:30px;bottom:34px;text-align:right;color:#fff;font-size:12px;font-weight:300;line-height:1.7}
  .letterhead__contact .line{display:flex;justify-content:flex-end;align-items:center;gap:6px}
  .letterhead__contact .addr{border-top:1px solid rgba(255,255,255,.6);margin-top:6px;padding-top:4px}
  .icon{width:11px;height:11px;fill:none;stroke:#fff;stroke-width:1.6}

  /* business cards */
  .card{width:420px;height:240px}
  .card--front{left:660px;top:204px}
  .card--back{left:660px;top:464px}
  .card--front .brand{position:absolute;left:36px;top:68px}
  .card .brand__dot{width:20px;height:20px}
  .card .brand__name{font-size:20px}
  .card__wave{position:absolute;right:0;top:0;width:420px;height:240px}
  .card__details{position:absolute;right:26px;top:58px;text-align:right;color:#fff}
  .card__name{font-size:17px;font-weight:600}
  .card__title{font-size:8px;opacity:.9;margin-bottom:14px}
  .card__small{font-size:8px;font-weight:300;line-height:1.8}
  .card--back .brand{position:absolute;inset:0;justify-content:center}
  .card--back .brand__name{font-size:24px}

  /* envelope */
  .envelope{left:660px;top:724px;width:480px;height:230px}
  .envelope .brand{position:absolute;left:28px;top:26px;align-items:flex-start}
  .envelope .brand__dot{width:18px;height:18px}
  .envelope .brand__name{font-size:18px}
  .envelope__addr{position:absolute;left:28px;top:90px;font-size:11px;line-height:1.4;color:#555}
  .envelope .watermark{right:40px;top:30px;width:170px;height:170px;
    background:radial-gradient(circle at 35% 60%,var(--mark-pink),transparent 62%),radial-gradient(circle at 65% 35%,var(--mark-teal),transparent 62%)}
</style>
</head>
<body>

<section class="sheet letterhead">
  <div class="brand">
    <div class="brand__row"><span class="brand__dot"></span><span class="brand__name">Lorvex Tilo</span></div>
    <span class="brand__tag">Tilo rise</span>
  </div>
  <div class="watermark" role="img" aria-label="Faint brand watermark"></div>

  <div class="letter">
    <div class="letter__to">To<br>The,<br>Director</div>
    <p>Lorem ipsum dolor sit amet, consectetur adipiscing elit. Sed at ante. Mauris eleifend, quam a vulputate dictum, massa quam dapibus leo, eget vulputate orci purus ut lorem. In fringilla mi in ligula. Pellentesque aliquam quam vel dolor. Nunc adipiscing. Sed quam odio, tempus ac, aliquam molestie varius ac, tellus. Vestibulum ut nulla aliquam risus rutrum interdum. Pellentesque lorem.</p>
    <p>Curabitur sit amet erat quis risus feugiat viverra. Pellentesque augue justo, sagittis et, lacinia at, venenatis non, arcu. Nunc nec libero. In cursus dictum risus. Etiam tristique nisl a nulla. Curabitur dolor nunc, egestas at, accumsan at, malesuada nec, magna. Vestibulum ante ipsum primis in faucibus orci luctus et ultrices. Integer orci vel mauris blandit vehicula. Nullam quis enim.</p>
    <p>In hac habitasse platea dictumst. Ut consequat, tellus eu volutpat dolor, sed imperdiet nulla tellus ut diam. Vestibulum ipsum erat sit amet, elit.</p>
    <div class="letter__close">Thanking you,</div>
    <span class="signature" role="img" aria-label="Handwritten signature of Mara Velt"></span>
  </div>

  <svg class="letterhead__wave" viewBox="0 0 560 260" preserveAspectRatio="none" aria-hidden="true">
    <defs>
      <linearGradient id="lhBand" x1="0" y1="1" x2="1" y2="0">
        <stop offset="0" stop-color="var(--dusk)"/>
        <stop offset=".55" stop-color="#a47ca2"/>
        <stop offset="1" stop-color="var(--magenta)"/>
      </linearGradient>
    </defs>
    <path d="M0 200 C180 200 330 170 420 70 C460 30 510 22 560 20 L560 260 L0 260Z" fill="url(#lhBand)"/>
    <path d="M0 176 C190 186 320 156 400 70 C440 28 500 8 560 6" fill="none" stroke="var(--teal)" stroke-width="4"/>
    <path d="M0 192 C190 198 330 168 412 78 C452 36 506 16 560 13" fill="none" stroke="var(--magenta)" stroke-width="2"/>
  </svg>
  <div class="letterhead__contact">
    <div class="line">555-014-2290 <svg class="icon" viewBox="0 0 12 12"><path d="M2 1h3l1 3-2 1a6 6 0 0 0 3 3l1-2 3 1v3a1 1 0 0 1-1 1A10 10 0 0 1 1 2a1 1 0 0 1 1-1z"/></svg></div>
    <div class="line">www.lorvextilo.com <svg class="icon" viewBox="0 0 12 12"><path d="M6 11s4-4 4-6.5A4 4 0 0 0 2 4.5C2 7 6 11 6 11z"/><circle cx="6" cy="4.5" r="1.4"/></svg></div>
    <div class="line">mara@lorvextilo.com <svg class="icon" viewBox="0 0 12 12"><rect x="1" y="2.5" width="10" height="7"/><path d="M1 2.5l5 4 5-4"/></svg></div>
    <div class="addr">Dummy city, Dummy country land</div>
  </div>
</section>

<section class="sheet card card--front">
  <div class="brand">
    <div class="brand__row"><span class="brand__dot"></span><span class="brand__name">Lorvex Tilo</span></div>
    <span class="brand__tag">Tilo rise</span>
  </div>
  <svg class="card__wave" viewBox="0 0 420 240" preserveAspectRatio="none" aria-hidden="true">
    <defs>
      <linearGradient id="cardBand" x1="0" y1="1" x2="1" y2="0">
        <stop offset="0" stop-color="var(--dusk)"/>
        <stop offset="1" stop-color="var(--magenta)"/>
      </linearGradient>
    </defs>
    <path d="M40 240 C150 230 200 200 220 130 C240 60 290 20 420 18 L420 240Z" fill="url(#cardBand)"/>
    <path d="M20 226 C130 214 185 190 206 126 C228 56 282 12 420 8" fill="none" stroke="var(--magenta)" stroke-width="2"/>
  </svg>
  <div class="card__details">
    <div class="card__name">Mara Velt</div>
    <div class="card__title">Director</div>
    <div class="card__small">555-014-2290<br>Dummy city, Dummy country land<br>W: www.lorvextilo.com | E: mara@lorvextilo.com</div>
  </div>
</section>

<section class="sheet card card--back">
  <div class="brand">
    <div class="brand__row"><span class="brand__dot"></span><span class="brand__name">Lorvex Tilo</span></div>
    <span class="brand__tag">Tilo rise</span>
  </div>
</section>

<section class="sheet envelope">
  <div class="brand">
    <div class="brand__row"><span class="brand__dot"></span><span class="brand__name">Lorvex Tilo</span></div>
    <span class="brand__tag">Tilo rise</span>
  </div>
  <div class="envelope__addr">Dummy city<br>Dummy country land</div>
  <div class="watermark" role="img" aria-label="Faint brand watermark"></div>
</section>

</body>
</html>
```